Visitenkarten-Design für Sonnen-/Fensterschutz
Zielgruppe
KLW GmbH ist eine Firma, die Sonnenschutz und Fensterschutz anbieten.
'Ihr kompetenter Partner in Sachen Sonnenschutz- , Fenster- und Türtechnik. Sie erhalten echtes Handwerk aus dem Mühlviertel zu fairen Preisen.'
Unsere Zielgruppe sind Personen mit Haus, die am Land leben.
Firmenname: KLW GmbH
Slogan: Fenster & Sonnenschutz
Aufgabenstellung
Hier befindet sich das Logodesign: https://dx.qv/t-QwLpo7RbNs
Bitte ein schlichtes Design bereitstellen mit einer Dummy-Person:
Jonas Weidlinger + Telefonnummer + Email
Die finalen Daten bitte erst am Schluss berücksichtigen (für Gewinnerdesign)
Gerne auch hintern + vorne bedruckbar bereitstellen.

```html
<!DOCTYPE html>
<html lang="de">
<head>
<meta charset="utf-8">
<title>KLW GmbH – Visitenkarte</title>
<link rel="stylesheet" href="https://fonts.googleapis.com/css2?family=Poppins:ital,wght@0,400;0,500;1,400;1,500&family=Kaushan+Script&display=swap">
<style>
  :root {
    --stage: #575757;
    --paper: #ffffff;
    --ink: #4a4a4a;
    --ink-soft: #5a5a5a;
    --brand-orange: #e2632a;
    --brand-red: #d52b26;
    --accent: #e0461f;
    --photo-top: #ece7e4;
    --photo-mid: #e2c39c;
    --photo-bottom: #efc6c3;
  }
  * { box-sizing: border-box; margin: 0; padding: 0; }
  html, body {
    width: 1200px; height: 1200px; overflow: hidden;
    background: var(--stage);
  }
  .canvas { position: relative; width: 1200px; height: 1200px; }

  .card { position: absolute; left: 280px; width: 669px; height: 433px; overflow: hidden; }

  /* Vorderseite */
  .card--front { top: 130px; background: var(--paper); font-family: "Poppins", sans-serif; }
  .portrait {
    position: absolute; left: 54px; top: 80px; width: 213px; height: 226px;
    background: linear-gradient(180deg, var(--photo-top) 0%, var(--photo-mid) 45%, var(--photo-bottom) 100%);
  }
  .person { position: absolute; left: 0; width: 320px; text-align: center; color: var(--ink); font-style: italic; }
  .person__name { top: 328px; font-size: 20px; font-weight: 400; }
  .person__role { top: 362px; font-size: 16px; font-weight: 500; }

  .divider { position: absolute; left: 310px; top: 28px; width: 4px; height: 378px; }

  .brand {
    position: absolute; left: 340px; top: 80px;
    display: flex; align-items: center; gap: 12px;
  }
  .brand__mark { width: 40px; height: 40px; background: var(--brand-orange); }
  .brand__name { font-size: 40px; font-weight: 500; color: var(--brand-orange); letter-spacing: 1px; line-height: 1; }

  .contact { position: absolute; left: 381px; top: 271px; color: var(--ink); font-style: italic; font-size: 16.5px; line-height: 23px; }
  .contact__company { font-size: 20px; margin-bottom: 6px; }
  .contact__company .highlight { color: var(--accent); }
  .contact__address { margin-bottom: 10px; }
  .contact__label { color: var(--accent); font-weight: 500; }
  .contact__line { margin-bottom: 5px; }

  /* Rückseite */
  .card--back {
    top: 635px;
    background: linear-gradient(90deg, var(--brand-orange) 0%, var(--brand-red) 78%, var(--brand-red) 100%);
  }
  .slogan {
    position: absolute; left: 40px; top: 180px; width: 590px;
    text-align: center; color: var(--paper);
    font-family: "Kaushan Script", cursive; font-size: 58px; line-height: 1;
    transform: rotate(-19deg);
  }
</style>
</head>
<body>
<main class="canvas">
  <section class="card card--front" aria-label="Visitenkarte Vorderseite">
    <div class="portrait" role="img" aria-label="Porträtfoto der Kontaktperson"></div>
    <p class="person person__name">Jonas Weidlinger</p>
    <p class="person person__role">Geschäftsführer</p>

    <svg class="divider" viewBox="0 0 4 378" preserveAspectRatio="none" aria-hidden="true">
      <path d="M2 0 L3.4 189 L2 378 L0.6 189 Z" fill="var(--brand-orange)"/>
    </svg>

    <div class="brand">
      <span class="brand__mark"></span>
      <span class="brand__name">KLW GmbH</span>
    </div>

    <div class="contact">
      <p class="contact__company"><span class="highlight">KLW</span> GmbH</p>
      <p class="contact__address">Am Lindenhang 22-24<br>30519 Erlenstadt</p>
      <p class="contact__line"><span class="contact__label">Tel.:</span>+49 160 482 3917</p>
      <p class="contact__line"><span class="contact__label">Mail:</span> klwfenster@beispielpost.de</p>
    </div>
  </section>

  <section class="card card--back" aria-label="Visitenkarte Rückseite">
    <p class="slogan">Fenster &amp; Sonnenschutz</p>
  </section>
</main>
</body>
</html>
```